redesign of my existing custom website into Wordpress based website

I need someone to redesign my current website into something more classy, simplistic, modern and on trend. I would like it set up on Wordpress in a way thats easy for me to make my own additions to blogs/price changes and promotion banners. I will also need a page that is password protected so members can login and have access to all my training videos and resources.
website is www.tidewellmamas.com.au

Target Market(s)

new mums

Industry/Entity Type

Fitness

Coding

Coded - Design and coding required

Number of Pages Required

5+ page

Colors
33a6d7

Requirements
Must have
• chic, modern, stylish and simplistic.
• a call to action above the page fold
• mobile friendly conversion
• a pop up message as soon as someone enters my sight offering my free report
• a members page that is password protected containing 3 youtube videos and 6 pdf attachments as resources
• a home page
• a contact us page
• an about us page
• a blog page
• a store page
Nice to have
• some examples of my peers websites that I like:
• www.norapellwick.com
• https://www.9qlr.com
• https://41bytedgarth.com
Should not have
• anything gimmicky

```html
<!DOCTYPE html>
<html lang="en">
<head>
<meta charset="utf-8">
<title>Tidewell Mamas – Home Fitness for New Mums</title>
<link href="https://fonts.googleapis.com/css2?family=Roboto:wght@300;400;500;700&display=swap" rel="stylesheet">
<style>
:root{
  --brand:#33a6d7;
  --brand-dark:#1f86b4;
  --pink:#e0267d;
  --pink-soft:#f6c6e1;
  --ink:#222;
  --muted:#bdbdbd;
  --dark:#262626;
  --black:#0c0c0c;
  --panel:#3a3a3a;
  --footer:#e2e2e2;
  --white:#fff;
}
*{box-sizing:border-box;margin:0;padding:0}
html,body{width:1200px;height:3814px;overflow:hidden}
body{position:relative;font-family:'Roboto',sans-serif;color:var(--white);background:var(--black)}
.abs{position:absolute}
.btn{position:absolute;display:flex;align-items:center;justify-content:center;background:var(--brand);color:var(--white);font-size:13px;font-weight:500;letter-spacing:.5px;text-transform:uppercase}
.ph{position:absolute}
/* top bar + nav */
.topbar{left:0;top:0;width:1200px;height:46px;background:var(--dark);font-size:12px;color:#ccc}
.topbar .contact{left:88px;top:15px;display:flex;gap:26px}
.topbar .cart{left:955px;top:15px}
.topbar .signin{left:1040px;top:11px;width:72px;height:26px;font-size:11px}
.nav{left:0;top:46px;width:1200px;height:61px;background:#161616}
.nav ul{list-style:none;position:absolute;top:22px;display:flex;gap:48px;font-size:14px;text-transform:uppercase;color:#aaa}
.nav .left{left:86px}.nav .right{left:700px}
.nav .active{color:var(--brand);font-weight:700}
.search{left:936px;top:16px;width:176px;height:30px;border:1px solid #666;font-size:12px;color:#999;padding:7px 10px}
.logo{left:535px;top:-6px;width:130px;height:130px;border-radius:50%;background:var(--white);display:flex;align-items:center;justify-content:center;text-align:center;color:var(--pink);font-size:17px;font-weight:500;line-height:1.2;z-index:2}
/* hero */
.hero{left:0;top:107px;width:1200px;height:574px;background:linear-gradient(100deg,#c9c0cf 0%,#a89db3 45%,#8e8398 100%)}
.hero h1{position:absolute;right:88px;top:165px;font-size:36px;font-weight:400;letter-spacing:1px;text-align:right}
.hero p{position:absolute;right:88px;top:212px;width:330px;font-size:14px;line-height:1.6;text-align:right;color:#eee}
.hero .btn{left:992px;top:273px;width:120px;height:40px}
.dots{left:560px;top:546px;display:flex;gap:10px}
.dots span{width:9px;height:9px;border-radius:50%;background:#ddd}
/* about */
.about{left:0;top:681px;width:1200px;height:387px;background:var(--black)}
.about h2{position:absolute;left:120px;top:80px;font-size:27px;font-weight:400;text-transform:uppercase;color:var(--muted)}
.about p{position:absolute;left:120px;top:125px;width:585px;font-size:13px;line-height:1.75;color:#aaa}
.about .btn{left:120px;top:260px;width:106px;height:40px}
.about .portrait{left:772px;top:102px;width:236px;height:236px;border-radius:50%;background:radial-gradient(circle,#9fd56b 0%,#6a8a4a 55%,#3c4a32 100%);border:4px solid #fff}
/* program */
.program{left:0;top:1068px;width:1200px;height:503px;background:var(--brand)}
.program h2{position:absolute;left:0;width:1200px;top:76px;text-align:center;font-size:26px;font-weight:400;text-transform:uppercase}
.card{top:150px;width:498px;height:242px;background:var(--white);color:var(--ink)}
.card .kicker{position:absolute;left:18px;top:34px;font-size:16px;text-transform:uppercase;color:#555}
.card .price{position:absolute;left:18px;top:62px;font-size:36px;font-weight:700;color:var(--brand)}
.card .save{position:absolute;left:18px;top:118px;font-size:12px;color:#999}
.card .weekly{position:absolute;left:18px;top:147px;font-size:13px;color:#777}
.card .weekly b{color:var(--pink);font-weight:500}
.card .go{position:absolute;left:18px;top:188px;font-size:11px;font-weight:700;color:#444}
.card .pack{position:absolute;left:290px;top:14px;width:190px;height:100px;background:linear-gradient(120deg,#f2a9cf,#9ccfe6,#f7e28a)}
.card .badge{position:absolute;left:212px;top:205px;width:64px;height:64px;border-radius:50%;color:#fff;font-size:12px;font-weight:700;display:flex;align-items:center;justify-content:center}
.card .tag{position:absolute;left:368px;top:185px;width:130px;height:57px;font-size:12px;font-weight:500;text-transform:uppercase;display:flex;align-items:center;justify-content:center}
/* why */
.why{left:0;top:1571px;width:600px;height:424px;background:var(--panel)}
.why h2{position:absolute;left:87px;top:36px;font-size:18px;font-weight:500;text-transform:uppercase;color:var(--brand)}
.why .item{position:absolute;left:87px;width:470px}
.why h3{font-size:15px;font-weight:500;color:#eee;margin-bottom:6px}
.why p{font-size:12px;line-height:1.55;color:#aaa}
.why a{display:block;font-size:11px;color:#ccc;margin-top:4px}
.video{left:600px;top:1571px;width:600px;height:424px;background:linear-gradient(160deg,#7b5a56,#4a3d3c 60%,#2a2a2a)}
.video p{position:absolute;left:0;width:600px;top:172px;text-align:center;font-size:15px;color:#eee}
.video svg{position:absolute;left:270px;top:210px}
/* before/after + reviews */
.results{left:0;top:1995px;width:1200px;height:382px;background:var(--black)}
.results h2{position:absolute;left:87px;top:62px;font-size:18px;font-weight:400;text-transform:uppercase;color:var(--muted)}
.arrows{left:612px;top:60px;display:flex;gap:8px}
.arrows span{width:20px;height:20px;background:#ccc;color:#333;font-size:12px;display:flex;align-items:center;justify-content:center}
.shot{top:120px;width:128px;height:150px;background:linear-gradient(180deg,#d8c2b0,#9e8676)}
.shot-label{top:283px;width:128px;text-align:center;font-size:10px;color:#aaa;text-transform:uppercase}
.review{left:710px;top:62px;width:402px;height:243px;background:var(--brand);text-align:center}
.review h3{margin-top:28px;font-size:17px;font-weight:400;text-transform:uppercase}
.review .avatar{position:absolute;left:163px;top:78px;width:76px;height:76px;border-radius:50%;background:radial-gradient(circle,#f0d2b8,#b98a6c);border:3px solid #fff}
.review p{position:absolute;left:60px;width:282px;top:170px;font-size:12px;line-height:1.5;color:#eef}
.review .name{position:absolute;left:0;width:402px;top:210px;font-size:11px;font-weight:500}
.review .prev,.review .next{position:absolute;top:108px;font-size:20px;color:#fff}
.review .prev{left:16px}.review .next{right:16px}
/* blog + gallery */
.blog{left:0;top:2377px;width:1200px;height:490px;background:var(--black)}
.blog h2{position:absolute;top:64px;font-size:17px;font-weight:500;text-transform:uppercase;color:var(--muted)}
.post{top:112px;width:273px}
.post .img{height:150px}
.post .date{position:absolute;left:110px;top:127px;width:52px;height:52px;border-radius:50%;background:var(--brand);border:3px solid #fff;font-size:10px;font-weight:700;display:flex;align-items:center;justify-content:center;text-align:center;line-height:1.1}
.post h3{margin-top:52px;font-size:14px;font-weight:500;color:#ddd}
.post p{font-size:11px;line-height:1.5;color:#999;margin-top:4px}
.post a{display:block;margin-top:10px;font-size:11px;font-weight:700;color:var(--brand)}
.gallery{left:697px;top:112px;width:415px;display:grid;grid-template-columns:repeat(3,128px);gap:16px 15px}
.gallery div{height:152px}
/* cta */
.cta{left:0;top:2867px;width:1200px;height:120px;background:var(--brand)}
.cta h2{position:absolute;left:172px;top:30px;font-size:24px;font-weight:500;text-transform:uppercase}
.cta p{position:absolute;left:172px;top:66px;font-size:17px;color:#e6f4fb}
.cta .btn{left:885px;top:38px;width:140px;height:40px;background:transparent;border:2px solid #fff;font-size:12px}
/* contact */
.contact{left:0;top:2987px;width:1200px;height:546px;background:var(--black)}
.contact h2{position:absolute;left:97px;width:693px;top:44px;text-align:center;font-size:22px;font-weight:400;text-transform:uppercase;color:var(--muted)}
.contact .lead{position:absolute;left:247px;width:393px;top:85px;text-align:center;font-size:12px;line-height:1.6;color:#aaa}
.field{position:absolute;background:#fff;color:#888;font-size:12px;padding:12px 14px}
.contact .btn{left:392px;top:443px;width:106px;height:40px;font-size:12px}
.contact .model{left:822px;top:22px;width:300px;height:524px;background:linear-gradient(180deg,#9fd56b 0%,#55713d 45%,#2e2e2e 100%);border-radius:150px 150px 0 0}
/* overlay + popup */
.overlay{left:0;top:0;width:1200px;height:3533px;background:rgba(0,0,0,.56);z-index:5}
.popup{left:374px;top:127px;width:437px;height:280px;background:var(--pink-soft);z-index:6;color:var(--ink);text-align:center}
.popup h2{margin-top:30px;font-size:22px;font-weight:500;text-transform:uppercase;color:#222}
.popup .sub{margin-top:4px;font-size:13px;color:#444}
.popup .field{left:49px;width:337px;height:42px;font-size:12px;text-align:left;border:1px solid #e9b6d3}
.popup .btn{left:160px;top:199px;width:116px;height:44px;font-size:14px;font-weight:700}
.popup .close{position:absolute;right:-14px;top:-10px;width:26px;height:26px;border-radius:50%;background:var(--brand);border:2px solid #fff;color:#fff;font-size:14px;font-weight:700;display:flex;align-items:center;justify-content:center}
/* footer */
.footer{left:0;top:3533px;width:1200px;height:229px;background:var(--footer);color:#555}
.footer .col{position:absolute;top:70px;width:190px;text-align:center;font-size:12px;line-height:1.45}
.footer .icon{width:46px;height:46px;border-radius:50%;border:2px solid var(--brand);margin:0 auto 12px;display:flex;align-items:center;justify-content:center}
.footer .brandmark{position:absolute;left:915px;top:46px;width:200px;text-align:center}
.footer .brandmark .dot{width:80px;height:80px;border-radius:50%;border:3px solid var(--pink);margin:0 auto 10px}
.footer .brandmark span{font-size:22px;color:var(--pink)}
.bottom{left:0;top:3762px;width:1200px;height:52px;background:#141414;font-size:11px;color:#888}
.bottom .copy{position:absolute;left:87px;top:20px}
.bottom .up{position:absolute;right:88px;top:17px;font-size:14px}
</style>
</head>
<body>

<header class="abs topbar">
  <div class="abs contact"><span>☎ 0412 555 019</span><span>✉ hello@tidewellmamas.com.au</span></div>
  <div class="abs cart">🛒 0 items</div>
  <div class="btn signin">Sign In</div>
</header>
<nav class="abs nav">
  <ul class="left"><li class="active">Home</li><li>About Us</li><li>Program</li><li>Store</li></ul>
  <ul class="right"><li>Blog</li><li>Contact</li></ul>
  <div class="abs search">Search Here</div>
</nav>
<div class="abs logo">Tidewell<br>Mamas</div>

<section class="abs hero">
  <div class="ph" role="img" aria-label="Mother exercising with hand weights beside her baby on a living room floor" style="inset:0"></div>
  <h1>TIDEWELL MAMAS</h1>
  <p>Get your body back after baby with a simple program you can do at home.</p>
  <div class="btn">Get Started</div>
  <div class="abs dots"><span></span><span></span><span></span><span></span><span></span></div>
</section>

<section class="abs about">
  <h2>About Marla Quinnell</h2>
  <p>After the birth of my daughter I struggled to find time for my health and felt lost in my own body. I created this program so mums can train at home, eat well and feel strong again without spending hours at a gym. With short workouts, simple recipes and a caring community, you can fit fitness around family life and finally feel like yourself again, one small step at a time.</p>
  <div class="btn">Read More</div>
  <div class="ph portrait" role="img" aria-label="Portrait of the trainer smiling in a green sports top"></div>
</section>

<section class="abs program">
  <h2>12 Week Home Workout Program For Mums!</h2>
  <article class="abs card" style="left:87px">
    <div class="kicker">One Time Only Payment Of</div>
    <div class="price">$89</div>
    <div class="save">Per saving $XX</div>
    <div class="weekly">Or pay only <b>$7.42</b> per week</div>
    <div class="go">GET STARTED →</div>
    <div class="pack" role="img" aria-label="Program booklets and meal guides"></div>
    <div class="badge" style="background:var(--pink)">FREE</div>
    <div class="tag" style="background:var(--pink);color:#fff">Basic Pack</div>
  </article>
  <article class="abs card" style="left:612px">
    <div class="kicker">One Time Only Payment Of</div>
    <div class="price">$199</div>
    <div class="save">Per saving $XX</div>
    <div class="weekly">Or pay only <b>$16.58</b> per week</div>
    <div class="go">GET STARTED →</div>
    <div class="pack" role="img" aria-label="Program booklets with home workout equipment"></div>
    <div class="badge" style="background:var(--brand)">FREE</div>
    <div class="tag" style="background:#f4dbe8;color:var(--pink)">Equipment Pack</div>
  </article>
</section>

<section class="abs why">
  <h2>Why Our Program Is Different</h2>
  <div class="item" style="top:78px"><h3>Specially Designed For Mums</h3><p>Short home workouts planned around naps, feeds and busy days, safe for the body after birth.</p><a>Read more</a></div>
  <div class="item" style="top:188px"><h3>Workout Equipment Included So You Can Train From Home</h3><p>Everything you need arrives at your door so you can train in the lounge room with baby close by.</p><a>Read more</a></div>
  <div class="item" style="top:298px"><h3>Delicious Low Fat Family Friendly Recipes</h3><p>Easy weekly meal plans the whole family will enjoy, with shopping lists to save you time.</p><a>Read more</a></div>
</section>
<section class="abs video" role="img" aria-label="Video still of a mum exercising with a resistance band at home">
  <p>Watch to learn more about this life changing program</p>
  <svg width="60" height="60" viewBox="0 0 60 60"><circle cx="30" cy="30" r="28" fill="#d33"/><path d="M24 18 L42 30 L24 42 Z" fill="#fff"/></svg>
</section>

<section class="abs results">
  <h2>Before And After Photo Book</h2>
  <div class="abs arrows"><span>‹</span><span>›</span></div>
  <div class="ph shot" role="img" aria-label="Before photo of a client" style="left:87px"></div>
  <div class="ph shot" role="img" aria-label="After photo of a client" style="left:227px"></div>
  <div class="ph shot" role="img" aria-label="Before photo of a second client" style="left:390px"></div>
  <div class="ph shot" role="img" aria-label="After photo of a second client" style="left:532px"></div>
  <div class="abs shot-label" style="left:87px">Before</div>
  <div class="abs shot-label" style="left:227px">After</div>
  <div class="abs shot-label" style="left:390px">Before</div>
  <div class="abs shot-label" style="left:532px">After</div>
  <aside class="abs review">
    <h3>Customer Reviews</h3>
    <span class="prev">‹</span><span class="next">›</span>
    <div class="avatar" role="img" aria-label="Customer portrait"></div>
    <p>I lost my baby weight and gained so much energy. The workouts fit perfectly into my day.</p>
    <div class="name">— JANE, MUM OF TWO</div>
  </aside>
</section>

<section class="abs blog">
  <h2 style="left:87px">Our Blog</h2>
  <h2 style="left:697px">Gallery</h2>
  <article class="abs post" style="left:87px">
    <div class="img" role="img" aria-label="Bowl of creamy pumpkin soup" style="background:linear-gradient(160deg,#f0e3d0,#d8a445)"></div>
    <div class="date">08<br>DEC</div>
    <h3>Creamy Pumpkin Soup</h3>
    <p>A warming soup the whole family will love, ready in thirty minutes.</p>
    <a>READ MORE »</a>
  </article>
  <article class="abs post" style="left:388px">
    <div class="img" role="img" aria-label="Tray of baked peaches" style="background:linear-gradient(160deg,#e9e2d6,#a5622f)"></div>
    <div class="date">05<br>DEC</div>
    <h3>Baked Peaches</h3>
    <p>A light sweet treat with no guilt, perfect after a family dinner.</p>
    <a>READ MORE »</a>
  </article>
  <div class="abs gallery">
    <div role="img" aria-label="Mum stretching at home" style="background:linear-gradient(#d9cfc4,#8a7a6c)"></div>
    <div role="img" aria-label="Mum and baby workout" style="background:linear-gradient(#bfb2a8,#6f5f55)"></div>
    <div role="img" aria-label="Mum lifting weights" style="background:linear-gradient(#c9a4b8,#7b5567)"></div>
    <div role="img" aria-label="Mum doing floor exercise" style="background:linear-gradient(#cdbfae,#7d6d5c)"></div>
    <div role="img" aria-label="Group of mums training" style="background:linear-gradient(#b9aaa0,#5e4f45)"></div>
    <div role="img" aria-label="Mum with baby on mat" style="background:linear-gradient(#d6b8c4,#8a6675)"></div>
  </div>
</section>

<section class="abs cta">
  <h2>Take The First Step Today By Joining Our Program</h2>
  <p>And I will help you bounce back to the body that you deserve!</p>
  <div class="btn">Get Started Now</div>
</section>

<section class="abs contact">
  <h2>Contact Form</h2>
  <p class="lead">If you have any questions or would like to reach me, please fill in your details below and we will get back to you shortly.</p>
  <div class="field" style="left:97px;top:173px;width:338px;height:40px">First Name</div>
  <div class="field" style="left:453px;top:173px;width:337px;height:40px">Last Name</div>
  <div class="field" style="left:97px;top:238px;width:338px;height:40px">Email</div>
  <div class="field" style="left:453px;top:238px;width:337px;height:40px">Phone</div>
  <div class="field" style="left:97px;top:303px;width:693px;height:110px">Message</div>
  <div class="btn">Submit Now</div>
  <div class="ph model" role="img" aria-label="Trainer standing with hands on hips in a green sports top"></div>
</section>

<div class="abs overlay"></div>
<div class="abs popup" role="dialog" aria-label="Free report">
  <div class="close">×</div>
  <h2>My Free Report</h2>
  <p class="sub">It is a long established fact that a reader ..its content</p>
  <div class="field" style="top:88px">Enter Your Name</div>
  <div class="field" style="top:143px">Enter Your E-mail</div>
  <div class="btn">Submit</div>
</div>

<footer class="abs footer">
  <div class="col" style="left:95px">
    <div class="icon"><svg width="20" height="20" viewBox="0 0 20 20"><path d="M10 1C6.5 1 4 3.6 4 7c0 4.5 6 12 6 12s6-7.5 6-12c0-3.4-2.5-6-6-6z" fill="#33a6d7"/><circle cx="10" cy="7" r="2.2" fill="#e2e2e2"/></svg></div>
    Tidewell Mamas<br>12 Harbourview Rd, Brisbane
  </div>
  <div class="col" style="left:285px">
    <div class="icon"><svg width="20" height="20" viewBox="0 0 20 20"><path d="M5 2l3 4-2 2c1 2 3 4 5 5l2-2 4 3-2 4C9 18 2 11 1 5z" fill="#33a6d7"/></svg></div>
    Give us a call<br>0412 555 019
  </div>
  <div class="col" style="left:475px">
    <div class="icon"><svg width="20" height="20" viewBox="0 0 20 20"><rect x="2" y="4" width="16" height="12" fill="#33a6d7"/><path d="M2 4l8 7 8-7" stroke="#e2e2e2" stroke-width="1.5" fill="none"/></svg></div>
    Send us a message<br>hello@tidewellmamas.com.au
  </div>
  <div class="col" style="left:665px">
    <div class="icon"><svg width="20" height="20" viewBox="0 0 20 20"><circle cx="10" cy="10" r="7" fill="none" stroke="#33a6d7" stroke-width="2"/><path d="M10 3v14M3 10h14" stroke="#33a6d7" stroke-width="1.5"/></svg></div>
    Follow us<br>■ ■
  </div>
  <div class="brandmark"><div class="dot"></div><span>Tidewell Mamas</span></div>
</footer>
<div class="abs bottom">
  <span class="copy">Copyright 2017 Tidewell Mamas. All Rights Reserved.</span>
  <span class="up">⌃</span>
</div>

</body>
</html>
```